Heron Haulage needs Bussiness cards!

Our new trucking company needs business cards!
We need the same design with two different names and emails, everything else it's the same.
I have included our original logo so we can use it for the design.
Note: the logo to be used is the o e with the buffalo on the right side, next to the letters H and H.

Target Market(s)

Trucking, refrigerated transportation, freight

Industry/Entity Type

Business

Contact Information for Business Card

Card #1:
Marcus Whitfield
marcuswhitfield@heronhaulage.example
1-855-317-6094
(956)238-7160
4117 W. Larkin Ave.
Pharr, TX 78590
www.heronhaulage.example

Card#2:
Rosalba Quintero
rosalba@heronhaulage.example
1-855-317-6094
(956)238-7160
4117 W. Larkin Ave.
Pharr, TX 78590
www.heronhaulage.example

Font styles to use
Sans Serif

Colors
0655a3
ec1f27
ffffff

Requirements
Must have
• our logo
Nice to have
• roads on background,

```html
<!DOCTYPE html>
<html lang="en">
<head>
<meta charset="utf-8">
<title>Heron Haulage – Business Cards</title>
<link rel="stylesheet" href="https://fonts.googleapis.com/css2?family=Open+Sans:wght@400;700;800&display=swap">
<style>
  :root {
    --navy: #0c2d5e;
    --blue: #0655a3;
    --red: #ec1f27;
    --white: #ffffff;
    --ink: #1d2a44;
    --backdrop: #2b2d31;
    --photo-top: #3a72b8;
    --photo-bottom: #3a3f48;
  }
  * { box-sizing: border-box; margin: 0; padding: 0; }
  html, body {
    width: 1200px; height: 864px; overflow: hidden;
    background: var(--backdrop);
    font-family: "Open Sans", Arial, sans-serif;
  }
  .sheet {
    position: relative; width: 1200px; height: 864px;
  }
  .card {
    position: absolute; left: 337px;
    width: 525px; height: 300px;
    border-radius: 4px; overflow: hidden;
    background: var(--white);
  }
  .card--front { top: 112px; }
  .card--back { top: 452px; }

  /* Front */
  .cover-photo {
    position: absolute; inset: 0;
    background: linear-gradient(to bottom, var(--photo-top), var(--photo-bottom));
  }
  .front-name {
    position: absolute; left: 0; right: 0; top: 70px;
    text-align: center;
    font-weight: 800; font-size: 40px; line-height: 1;
    color: var(--white);
    letter-spacing: 0.5px;
  }

  /* Back */
  .back-brand {
    position: absolute; right: 42px; top: 52px;
    display: flex; align-items: center; gap: 10px;
    font-weight: 800; font-size: 30px; line-height: 1;
    color: var(--navy);
  }
  .back-brand .mark {
    width: 22px; height: 22px; border-radius: 50%;
    background: var(--red);
  }
  .holder {
    position: absolute; left: 36px; top: 128px;
    font-weight: 700; font-size: 17px; line-height: 1;
  }
  .holder .first { color: var(--navy); }
  .holder .last { color: var(--red); }
  .divider {
    position: absolute; left: 0; right: 0; top: 152px;
    height: 1px; background: var(--red);
  }
  .contacts {
    position: absolute; right: 28px; top: 170px;
    list-style: none;
    font-size: 13px; line-height: 21px; color: var(--ink);
    text-align: right;
  }
  .contacts li {
    display: flex; justify-content: flex-end; align-items: center; gap: 7px;
  }
  .contacts svg { width: 11px; height: 11px; flex: none; }
  .icon { fill: var(--red); }
</style>
</head>
<body>
<main class="sheet">

  <section class="card card--front">
    <div class="cover-photo" role="img" aria-label="Photograph of an empty straight highway stretching to the horizon under a blue sky with clouds"></div>
    <div class="front-name">Heron Haulage</div>
  </section>

  <section class="card card--back">
    <div class="back-brand"><span>Heron Haulage</span><span class="mark"></span></div>
    <p class="holder"><span class="first">Marcus</span> <span class="last">Whitfield</span></p>
    <div class="divider"></div>
    <ul class="contacts">
      <li>1-855-317-6094
        <svg viewBox="0 0 12 12" aria-hidden="true"><path class="icon" d="M2.5 1 4.5 3 3.6 4.4c.8 1.6 2.1 2.9 3.7 3.7L8.7 7.2 11 9.2 9.8 11C5 10.7 1.3 7 1 2.2Z"/></svg>
      </li>
      <li>(956)238-7160
        <svg viewBox="0 0 12 12" aria-hidden="true"><path class="icon" d="M3 0.5h6v11H3Zm1 1.5v7h4V2Z"/></svg>
      </li>
      <li>marcuswhitfield@heronhaulage.example
        <svg viewBox="0 0 12 12" aria-hidden="true"><path class="icon" d="M0.5 2.5h11v7h-11Zm1 1v.4L6 6.8l4.5-2.9v-.4Z"/></svg>
      </li>
      <li>www.heronhaulage.example
        <svg viewBox="0 0 12 12" aria-hidden="true"><circle class="icon" cx="6" cy="6" r="5.5"/><path d="M0.5 6h11M6 .5c-2.4 3-2.4 8 0 11m0-11c2.4 3 2.4 8 0 11" stroke="#fff" stroke-width=".8" fill="none"/></svg>
      </li>
      <li>4117 W. Larkin Ave. Pharr, TX 78590
        <svg viewBox="0 0 12 12" aria-hidden="true"><path class="icon" d="M6 .5a4 4 0 0 1 4 4c0 3-4 7-4 7s-4-4-4-7a4 4 0 0 1 4-4Zm0 2.3a1.7 1.7 0 1 0 0 3.4 1.7 1.7 0 0 0 0-3.4Z"/></svg>
      </li>
    </ul>
  </section>

</main>
</body>
</html>
```